Business card for a Exhibition booth fabrication company

Hi. My company would like to change our corporate name card. We are an events and Exhibition stand builder company. We would like our corporate name card to resonate what we do. I need someone to create something unique that relates to the industry that I am in. The graphic designer should be creative to incorporate the elements of my industry and try to blend in well in the design of the card. Our aim is to ensure that we are unique and our card can look different from our competitors.
Updates

Target Market(s)

Marketing and events manager from all companies

Contact Information for Business Card

The business card should have the following details:
Name
Job Title
Email
Website

Colors

Designer to choose colors to be used in the design.

Requirements
Must have
• The card must be look something that is relevant to the service that I am providing. My website is: www.velmora-buildworks.com
• You can see my website to get more information on what service that I am doing
Nice to have
• On the back of my card, I would like to have a globe image with the incorporation of my company logo. This is to indicate that my services can be done in any part of the world.

```html
<!DOCTYPE html>
<html lang="en">
<head>
<meta charset="utf-8">
<title>Velmora Buildworks – Business Card</title>
<link href="https://fonts.googleapis.com/css2?family=Open+Sans:wght@400;600;700&display=swap" rel="stylesheet">
<style>
  :root {
    --bg: #e9e6e1;
    --white: #f7f7f6;
    --red: #e0252b;
    --red-dark: #c81d23;
    --grey: #6d6e70;
    --grey-text: #7a7b7d;
    --charcoal: #2c2c2e;
    --charcoal-deep: #1f1f21;
    --ink-light: #eeeeee;
  }
  * { box-sizing: border-box; margin: 0; padding: 0; }
  html, body { width: 1200px; height: 780px; overflow: hidden; }
  body {
    background: var(--bg);
    font-family: "Open Sans", Arial, sans-serif;
    display: flex;
    align-items: center;
    justify-content: center;
    gap: 40px;
  }
  .card {
    width: 540px;
    height: 310px;
    position: relative;
    overflow: hidden;
    box-shadow: 0 6px 18px rgba(0,0,0,0.18);
  }

  /* Front */
  .card--front { background: var(--white); display: flex; flex-direction: column; }
  .front__brand {
    height: 150px;
    display: flex;
    align-items: center;
    gap: 14px;
    padding-left: 48px;
  }
  .brand-dot { width: 22px; height: 22px; border-radius: 50%; background: var(--red); }
  .brand-name {
    font-size: 22px;
    font-weight: 600;
    letter-spacing: 0.22em;
    color: var(--grey-text);
    text-transform: uppercase;
  }
  .front__band {
    flex: 1;
    background: var(--red);
    display: flex;
    align-items: center;
    padding: 0 48px;
    color: #fff;
  }
  .person { padding-right: 28px; }
  .person__name { font-size: 24px; font-weight: 700; line-height: 1.1; }
  .person__title { font-size: 14px; font-weight: 400; text-align: right; }
  .band-divider { width: 2px; height: 62px; background: rgba(255,255,255,0.85); }
  .contacts { list-style: none; padding-left: 26px; font-size: 13px; line-height: 1.75; }
  .contacts li { display: flex; align-items: center; gap: 8px; }
  .contacts svg { width: 12px; height: 12px; flex: none; }
  .front__address {
    height: 44px;
    background: var(--grey);
    border-top: 2px solid #fff;
    color: #f1f1f1;
    font-size: 14px;
    letter-spacing: 0.08em;
    display: flex;
    align-items: center;
    padding-left: 48px;
  }

  /* Back */
  .card--back {
    background: linear-gradient(135deg, var(--charcoal) 0%, var(--charcoal-deep) 100%);
    color: var(--ink-light);
  }
  .back__globe {
    position: absolute;
    top: 20px; left: 170px;
    width: 300px; height: 200px;
    border-radius: 50%;
    background: radial-gradient(ellipse at center, rgba(255,255,255,0.07) 0%, rgba(255,255,255,0) 70%);
  }
  .back__content { position: relative; padding: 34px 40px 0; }
  .back__brand { display: flex; align-items: center; gap: 12px; margin-bottom: 22px; }
  .back__brand .brand-name { color: #fff; font-size: 24px; font-weight: 700; letter-spacing: 0.16em; }
  .services { list-style: none; font-size: 12.5px; line-height: 1.7; color: var(--ink-light); }
  .back__web {
    position: absolute;
    left: 40px; bottom: 40px;
    font-size: 13px;
    letter-spacing: 0.06em;
    color: var(--red);
  }
  .back__strip {
    position: absolute;
    left: 0; right: 0; bottom: 0;
    height: 26px;
    background: var(--red-dark);
    border-top: 2px solid #fff;
  }
</style>
</head>
<body>

  <section class="card card--front" aria-label="Business card front">
    <div class="front__brand">
      <span class="brand-dot"></span>
      <span class="brand-name">Velmora Buildworks</span>
    </div>
    <div class="front__band">
      <div class="person">
        <p class="person__name">Daniel Okafor</p>
        <p class="person__title">Director</p>
      </div>
      <span class="band-divider"></span>
      <ul class="contacts">
        <li>
          <svg viewBox="0 0 12 12"><rect x="1" y="1" width="10" height="10" fill="none" stroke="#fff" stroke-width="1.6"/></svg>
          (555) 014 2286
        </li>
        <li>
          <svg viewBox="0 0 12 12"><rect x="0.8" y="2" width="10.4" height="8" fill="#fff"/><path d="M1 2.5 L6 7 L11 2.5" fill="none" stroke="#e0252b" stroke-width="1"/></svg>
          info@velmora-buildworks.com
        </li>
        <li>
          <svg viewBox="0 0 12 12"><circle cx="6" cy="6" r="5.2" fill="none" stroke="#fff" stroke-width="1.2"/><ellipse cx="6" cy="6" rx="2.2" ry="5.2" fill="none" stroke="#fff" stroke-width="1"/><line x1="0.8" y1="6" x2="11.2" y2="6" stroke="#fff" stroke-width="1"/></svg>
          www.velmora-buildworks.com
        </li>
      </ul>
    </div>
    <div class="front__address">PO BOX 418, Harlow Street, 4th Lane, Arizona</div>
  </section>

  <section class="card card--back" aria-label="Business card back">
    <div class="back__globe" role="img" aria-label="Faint world map showing global reach"></div>
    <div class="back__content">
      <div class="back__brand">
        <span class="brand-dot"></span>
        <span class="brand-name">Velmora Buildworks</span>
      </div>
      <ul class="services">
        <li>Exhibition Booth Fabrication | Outdoor Booth Setup | Interior Design</li>
        <li>Installation and Dismantle | Exhibition Management</li>
        <li>Shell Scheme Display Booth | Custom Stand Design</li>
        <li>Exhibition Furniture and Equipment | Exhibition Project Management</li>
      </ul>
    </div>
    <p class="back__web">WWW.VELMORA-BUILDWORKS.com</p>
    <div class="back__strip"></div>
  </section>

</body>
</html>
```